Local Flower Farm Needs Business Card Design

I need business cards designed for a flower farm based in Eudora, Kansas.
Business Info:
We are a local cut flower farm located in Eudora, Kansas, founded by Corinne Haldwick. What started as a passion for agriculture and search for more joy in daily life has blossomed into a small business dedicated to providing the community with beautiful, fresh, and sustainable flowers. We specialize in local, seasonal blooms, ensuring that every petal reflects the care and dedication we pour into our craft. Our mission is to deliver the highest quality flowers directly to our customers through local farmers markets and to florists who share our commitment to sustainability. Join us in celebrating the beauty of nature, one bloom at a time!
Contact Details:
Corinne Haldwick
Owner
Phone 913-555-0147
Facebook: Rosalind Thorpe Gardens
Instagram: @RosalindThorpeGardens
Website: RosalindThorpeGardens.example
Target Market(s)
Wholesale to Florists and Direct to Consumer via Farmers Market
Industry/Entity Type
Florist, Farm
Contact Information for Business Card
Name, Contact Info, Logo
Look and feel
Each slider illustrates characteristics of the customer's brand and the style your logo design should communicate.

```html
<!DOCTYPE html>
<html lang="en">
<head>
<meta charset="utf-8">
<title>Rosalind Thorpe Gardens — Business Card</title>
<link rel="stylesheet" href="https://fonts.googleapis.com/css2?family=Montserrat:wght@400;500;700&display=swap">
<style>
  :root {
    --ink: #0c2a2b;
    --paper: #ffffff;
    --backdrop: #e8e5df;
    --card-shadow: rgba(0, 0, 0, 0.18);
  }
  * { box-sizing: border-box; margin: 0; padding: 0; }
  html, body {
    width: 900px; height: 1200px; overflow: hidden;
    background: var(--backdrop);
    font-family: "Montserrat", Arial, sans-serif;
    color: var(--ink);
  }
  .card {
    position: absolute; left: 80px; width: 742px; height: 440px;
    border-radius: 22px;
    box-shadow: 0 6px 18px var(--card-shadow);
    overflow: hidden;
  }
  .card--front { top: 131px; background: var(--paper); }
  .card--back  { top: 639px; background: var(--ink); }

  .seal {
    position: absolute; border-radius: 50%;
    display: flex; align-items: center; justify-content: center;
    text-align: center; font-weight: 500; text-transform: uppercase;
  }
  .seal--small {
    left: 41px; top: 37px; width: 154px; height: 154px;
    border: 1px solid var(--ink); color: var(--ink);
    font-size: 15px; line-height: 1.35; letter-spacing: 1.5px;
  }
  .seal--back {
    left: 216px; top: 66px; width: 310px; height: 310px;
    border: 1.2px solid var(--paper); color: var(--paper);
    font-size: 26px; line-height: 1.35; letter-spacing: 3px;
  }

  .brand-feature {
    position: absolute; left: 375px; top: 40px; width: 335px; height: 380px;
    display: flex; flex-direction: column; justify-content: center;
    font-weight: 500; font-size: 54px; line-height: 1.12; color: var(--ink);
    text-transform: uppercase; letter-spacing: 1px;
  }

  .owner { position: absolute; left: 39px; top: 240px; }
  .owner__name { font-size: 23px; font-weight: 700; line-height: 1.2; }
  .owner__role { font-size: 15px; font-weight: 400; margin-top: 2px; }

  .contacts { position: absolute; left: 39px; top: 308px; list-style: none; }
  .contacts li {
    display: flex; align-items: center; gap: 9px;
    font-size: 15px; height: 25.5px;
  }
  .contacts svg { width: 15px; height: 15px; flex: none; }
  .dot { width: 13px; height: 13px; border-radius: 50%; background: var(--ink); flex: none; margin: 0 1px; }
</style>
</head>
<body>

<section class="card card--front" aria-label="Business card front">
  <div class="seal seal--small">Rosalind<br>Thorpe<br>Gardens</div>

  <div class="owner">
    <h1 class="owner__name">Corinne Haldwick</h1>
    <p class="owner__role">Owner</p>
  </div>

  <ul class="contacts">
    <li>
      <svg viewBox="0 0 24 24" aria-hidden="true"><path fill="var(--ink)" d="M6.6 10.8a15.2 15.2 0 0 0 6.6 6.6l2.2-2.2a1 1 0 0 1 1-.25 11.4 11.4 0 0 0 3.6.57 1 1 0 0 1 1 1V20a1 1 0 0 1-1 1A17 17 0 0 1 3 4a1 1 0 0 1 1-1h3.5a1 1 0 0 1 1 1c0 1.25.2 2.45.57 3.57a1 1 0 0 1-.25 1z"/></svg>
      913-555-0147
    </li>
    <li><span class="dot"></span>Rosalind Thorpe Gardens</li>
    <li><span class="dot"></span>@RosalindThorpeGardens</li>
    <li>
      <svg viewBox="0 0 24 24" aria-hidden="true"><circle cx="12" cy="12" r="10" fill="none" stroke="var(--ink)" stroke-width="2.2"/><ellipse cx="12" cy="12" rx="4.2" ry="10" fill="none" stroke="var(--ink)" stroke-width="2"/><path d="M2 12h20" stroke="var(--ink)" stroke-width="2"/></svg>
      www.RosalindThorpeGardens.example
    </li>
  </ul>

  <div class="brand-feature">Rosalind<br>Thorpe<br>Gardens</div>
</section>

<section class="card card--back" aria-label="Business card back">
  <div class="seal seal--back">Rosalind<br>Thorpe<br>Gardens</div>
</section>

</body>
</html>
```